Retail Sign for Houseplant Campaign

Sign will measure 3 to 4 foot tall by 22.2inches and place on rolling racks of houseplants for a retail promotion in The Birchwell Yard. The theme of the promotion will be "New Year, New You!" Selling points which should be on the sign are Houseplants give you a taste of nature, Houseplants boost air quality inside your home, Indoor plants reduce anxiety, Indoor plants make you more productive, Houseplants improve your concentration and memory.
Updates

Target Market(s)

People who love plants

Industry/Entity Type

Horticulture/ retail

Colors
00AB8E
00BBA5
67D7C9
C6EFE9
E9F9F6
59FF00
82FF00
B8FF75
E3FFCB
F4FFEA
FFF300
FFF600
FEFA6F
FFFEC7
FFFEE8

Requirements
Must have
• Must feel energetic and encourage people to buy plants. Should include 1-2 photos and the selling points listed

```html
<!DOCTYPE html>
<html lang="en">
<head>
<meta charset="utf-8">
<title>New Year, New You! – Houseplant Sign</title>
<link href="https://fonts.googleapis.com/css2?family=Sacramento&family=Alegreya:ital@1&display=swap" rel="stylesheet">
<style>
  :root {
    --canvas: #ffffff;
    --frame-line: #c9c9c9;
    --header-bg: #f0fde6;
    --title-ink: #135f6b;
    --accent-top: #00ab8e;
    --teal-deep: #139181;
    --teal-bright: #00b39a;
    --olive: #8a8426;
    --leaf-green: #078a22;
    --panel-text: #ffffff;
  }
  * { box-sizing: border-box; margin: 0; padding: 0; }
  html, body { width: 763px; height: 1200px; overflow: hidden; background: var(--canvas); }
  .sign {
    position: relative; width: 763px; height: 1200px;
    background: var(--canvas); border: 1px solid var(--frame-line);
  }
  .sign-frame {
    position: absolute; left: 25px; top: 23px; width: 715px; height: 1154px;
    border: 1px solid var(--frame-line);
  }
  .header {
    position: absolute; left: 25px; top: 23px; width: 715px; height: 229px;
    background: var(--header-bg);
  }
  .header-tab {
    position: absolute; left: 273px; top: 0; width: 168px; height: 17px;
    background: var(--accent-top);
  }
  .campaign-title {
    position: absolute; left: 0; top: 42px; width: 100%;
    text-align: center; font-family: "Sacramento", cursive;
    font-weight: 400; font-size: 84px; line-height: 1; color: var(--title-ink);
    white-space: nowrap;
  }
  .plant-border {
    position: absolute; left: 4px; top: 117px; width: 707px; height: 112px;
    background: linear-gradient(180deg, rgba(240,253,230,0) 0%, #dfeed4 55%, #c9dcbc 100%);
  }
  .tile {
    position: absolute; width: 357px; height: 232px;
  }
  .tile.left { left: 25.5px; }
  .tile.right { left: 382.5px; }
  .row-1 { top: 257px; height: 228px; }
  .row-2 { top: 485px; }
  .row-3 { top: 717px; }
  .row-4 { top: 949px; height: 228px; }
  .selling-point {
    display: flex; align-items: center; justify-content: center; text-align: center;
    font-family: "Alegreya", serif; font-style: italic; font-size: 31px;
    line-height: 41px; color: var(--panel-text); padding: 0 20px;
  }
  .bg-teal-deep { background: var(--teal-deep); }
  .bg-teal-bright { background: var(--teal-bright); }
  .bg-olive { background: var(--olive); }
  .bg-leaf { background: var(--leaf-green); }
  .photo-plant-shelf { background: linear-gradient(120deg, #f3f3f1 0%, #e5ddd2 50%, #b9b6b4 100%); }
  .photo-monstera { background: linear-gradient(110deg, #8a6f58 0%, #ece8e3 45%, #2f5a2c 100%); }
  .photo-watering { background: linear-gradient(115deg, #efefef 0%, #c7c9ca 45%, #41573f 100%); }
  .photo-relaxing { background: linear-gradient(160deg, #f2f2f0 0%, #dedad3 50%, #a9b5c4 100%); }
  .accent-bar { position: absolute; width: 13px; height: 130px; }
  .accent-bar.on-right { left: 726px; }
  .accent-bar.on-left { left: 25.5px; }
</style>
</head>
<body>
<main class="sign">
  <header class="header">
    <div class="header-tab"></div>
    <h1 class="campaign-title">New Year, New You!"</h1>
    <div class="plant-border" role="img" aria-label="Row of line-drawn potted houseplants in soft sage green"></div>
  </header>

  <p class="tile left row-1 selling-point bg-teal-deep">Houseplants<br>give you a taste<br>of nature</p>
  <div class="tile right row-1 photo-plant-shelf" role="img" aria-label="Photo of a woman placing a croton plant on a white shelf"></div>

  <div class="tile left row-2 photo-monstera" role="img" aria-label="Photo of a smiling woman wiping the leaves of a monstera plant"></div>
  <p class="tile right row-2 selling-point bg-teal-bright">Houseplants<br>boost air quality<br>inside your home</p>

  <p class="tile left row-3 selling-point bg-olive">Indoor plants<br>reduce anxiety,<br>Indoor plants make<br>you more productive</p>
  <div class="tile right row-3 photo-watering" role="img" aria-label="Photo of a mother and daughter watering a snake plant"></div>

  <div class="tile left row-4 photo-relaxing" role="img" aria-label="Photo of a woman relaxing on the floor beside potted plants and a laptop"></div>
  <p class="tile right row-4 selling-point bg-leaf">Houseplants<br>improve your<br>concentration<br>and memory</p>

  <div class="accent-bar on-right bg-teal-deep" style="top:305px"></div>
  <div class="accent-bar on-left bg-teal-bright" style="top:536px"></div>
  <div class="accent-bar on-right bg-olive" style="top:768px"></div>
  <div class="accent-bar on-left bg-leaf" style="top:1000px"></div>

  <div class="sign-frame"></div>
</main>
</body>
</html>
```